Stationary - Based On Previous Design

Basic stationary with a header and footer

Target Market(s)

Friends, Colleagues, More friendly than professional

Industry/Entity Type

legal/personal

Colors
00AB8E
00BBA5
67D7C9
C6EFE9
E9F9F6

Requirements
Must have
• Green & White
Nice to have
• I like the "G" on the business card and was thinking that would be for both G's in "PellaNote"
Should not have
• other colors

```html
<!DOCTYPE html>
<html lang="en">
<head>
<meta charset="utf-8">
<title>PellaNote Stationery</title>
<link rel="stylesheet" href="https://fonts.googleapis.com/css2?family=Roboto:wght@300;400;500&family=Outfit:wght@400;500;600;700&family=Mrs+Saint+Delafield&display=swap">
<style>
  :root {
    --teal: #1db3a0;
    --teal-deep: #00ab8e;
    --teal-soft: #c6efe9;
    --white: #ffffff;
    --ink: #222222;
    --ink-soft: #555555;
    --logo-grey: #555555;
    --accent-red: #e8402f;
    --ghost: #f1f1f1;
    --backdrop: #4b4b50;
  }
  * { box-sizing: border-box; margin: 0; padding: 0; }
  html, body { width: 1200px; height: 1082px; overflow: hidden; }
  body { background: var(--backdrop); position: relative; font-family: "Roboto", sans-serif; }

  .letterhead {
    position: absolute; left: 100px; top: 140px; width: 564px; height: 799px;
    background: var(--white); overflow: hidden;
  }
  .ghost-mark {
    position: absolute; border-radius: 50%; background: var(--ghost);
  }
  .letterhead .ghost-mark { width: 230px; height: 230px; right: -80px; top: -40px; }

  .wordmark {
    position: absolute; display: flex; align-items: center; gap: 8px;
    font-family: "Outfit", sans-serif; font-weight: 700; color: var(--teal);
  }
  .wordmark .dot { border-radius: 50%; background: var(--teal); flex: none; }
  .letterhead .wordmark { left: 31px; top: 40px; font-size: 30px; }
  .letterhead .wordmark .dot { width: 30px; height: 30px; }

  .sender { position: absolute; left: 42px; top: 163px; color: var(--ink); }
  .sender .name { font-size: 11.5px; font-weight: 500; }
  .sender .name span { color: var(--accent-red); font-weight: 400; }
  .sender .role { font-size: 9.5px; font-weight: 300; margin-top: 5px; }
  .sender .lines { margin-top: 10px; font-size: 10.6px; font-weight: 300; line-height: 17.8px; }
  .sender .lines b { font-weight: 500; }
  .sender .lines .red { color: var(--accent-red); }

  .date { position: absolute; right: 39px; top: 234px; font-size: 10.6px; font-weight: 300; color: var(--ink); }

  .body-copy {
    position: absolute; left: 42px; top: 297px; width: 483px;
    font-size: 10.4px; font-weight: 300; line-height: 18.7px; color: var(--ink-soft);
    text-align: justify; hyphens: auto;
  }
  .body-copy p + p { margin-top: 18.7px; }

  .sign-off { position: absolute; left: 42px; top: 650px; color: var(--ink); }
  .sign-off .script { font-family: "Mrs Saint Delafield", cursive; font-size: 26px; line-height: 1; }
  .sign-off .name { font-size: 11.5px; font-weight: 500; margin-top: 6px; }
  .sign-off .role { font-size: 10.4px; font-weight: 300; margin-top: 4px; }

  .footer-band {
    position: absolute; left: 0; right: 0; top: 742px; height: 33px;
    background: var(--teal); display: flex; align-items: center; gap: 16px;
    padding-left: 39px; font-family: "Outfit", sans-serif; font-size: 9.4px; color: var(--white);
  }
  .footer-band .item { display: flex; align-items: center; gap: 5px; }
  .footer-band .item.name { font-weight: 600; }
  .icon { width: 14px; height: 14px; flex: none; }

  .card { position: absolute; left: 738px; width: 380px; height: 217px; overflow: hidden; }
  .card-front { top: 467px; background: var(--teal); }
  .card-front .wordmark { color: var(--white); font-size: 40px; left: 92px; top: 80px; gap: 12px; }
  .card-front .wordmark .dot { width: 40px; height: 40px; background: var(--white); }

  .card-back { top: 722px; background: var(--white); }
  .card-back .ghost-mark { width: 170px; height: 170px; right: -50px; top: 10px; }
  .card-back .wordmark { left: 27px; top: 33px; font-size: 24px; }
  .card-back .wordmark .dot { width: 24px; height: 24px; }
  .card-back .holder { position: absolute; left: 29px; top: 96px; font-family: "Outfit", sans-serif; }
  .card-back .holder .name { font-size: 18px; font-weight: 600; color: var(--logo-grey); }
  .card-back .holder .role { font-size: 12px; font-weight: 500; color: var(--teal); margin-top: 2px; }
  .card-back .rule { width: 46px; height: 1px; background: #bdbdbd; margin: 10px 0 9px; }
  .card-back .contact { display: flex; align-items: center; gap: 6px; font-size: 12px; color: var(--logo-grey); line-height: 20px; }
  .card-back .contact .icon { width: 11px; height: 11px; }
</style>
</head>
<body>

<section class="letterhead">
  <div class="ghost-mark" aria-hidden="true"></div>
  <div class="wordmark"><span class="dot"></span>PellaNote</div>

  <div class="sender">
    <div class="name">Clara <span>Benton</span></div>
    <div class="role">Designer</div>
    <div class="lines">
      <div><b class="red">A :</b> New York City- Zip Code - 000</div>
      <div><b>W :</b> www.yourwebsitename.com</div>
      <div><b class="red">P :</b> +000 123 456 789</div>
    </div>
  </div>

  <div class="date">Date : 25 September, 2030</div>

  <div class="body-copy">
    <p>Lorem ipsum dolor sit amet, consectetur adipisicing elit, sed do eiusmod tempor incididunt ut labore et dolore magna aliqua. Ut enim ad minim veniam, quis nostrud exercitation ullamco laboris nisi ut aliquip ex ea commodo consequat.</p>
    <p>Excepteur sint occaecat cupidatat non proident, sunt in culpa qui officia deserunt mollit anim id est laborum. Sed ut perspiciatis unde omnis iste natus error sit voluptatem accusantium doloremque laudantium, totam rem aperiam, eaque ipsa quae ab illo inventore veritatis et quasi architecto beatae vitae dicta sunt explicabo. Nemo enim ipsam voluptatem quia voluptas sit aspernatur aut odit aut quia consequuntur voluptatem sequi nesciunt.</p>
    <p>Voluptatem accusantium doloremque laudantium, totam rem aperiam, eaque ipsa quae ab illo inventore veritatis et quasi architecto beatae vitae dicta sunt explicabo. Nemo enim ipsam voluptatem quia voluptas sit aspernatur aut odit aut quia consequuntur voluptatem sequi nesciunt.</p>
    <p>Neque porro quisquam dolorem ipsum quia dolor sit amet, consecteturtempora incidunt labore dolore magnam aliquam quaerat voluptatem.</p>
  </div>

  <div class="sign-off">
    <div class="script">Daniel Reyes</div>
    <div class="name">Daniel Reyes</div>
    <div class="role">Manager</div>
  </div>

  <footer class="footer-band">
    <div class="item name">
      <svg class="icon" viewBox="0 0 14 14" aria-hidden="true"><circle cx="7" cy="7" r="6.5" fill="#fff"/></svg>
      Marta Lindqvist
    </div>
    <div class="item">
      <svg class="icon" viewBox="0 0 14 14" aria-hidden="true"><circle cx="7" cy="7" r="6.5" fill="#fff"/><rect x="3.6" y="4.6" width="6.8" height="4.8" fill="none" stroke="#1db3a0" stroke-width="0.9"/><path d="M3.6 4.6 7 7.4 10.4 4.6" fill="none" stroke="#1db3a0" stroke-width="0.9"/></svg>
      mlindqvist@lindqvistnotes.com
    </div>
    <div class="item">
      <svg class="icon" viewBox="0 0 14 14" aria-hidden="true"><circle cx="7" cy="7" r="6.5" fill="#fff"/><path d="M7 3.2a2.4 2.4 0 0 1 2.4 2.4C9.4 7.4 7 10.4 7 10.4S4.6 7.4 4.6 5.6A2.4 2.4 0 0 1 7 3.2z" fill="#1db3a0"/><circle cx="7" cy="5.6" r="0.9" fill="#fff"/></svg>
      418 Alder Row Brookfield, OR 97214
    </div>
  </footer>
</section>

<section class="card card-front">
  <div class="wordmark"><span class="dot"></span>PellaNote</div>
</section>

<section class="card card-back">
  <div class="ghost-mark" aria-hidden="true"></div>
  <div class="wordmark"><span class="dot"></span>PellaNote</div>
  <div class="holder">
    <div class="name">Marta Lindqvist</div>
    <div class="role">President</div>
    <div class="rule"></div>
    <div class="contact">
      <svg class="icon" viewBox="0 0 14 14" aria-hidden="true"><circle cx="7" cy="7" r="6.5" fill="#1db3a0"/><rect x="3.6" y="4.6" width="6.8" height="4.8" fill="none" stroke="#fff" stroke-width="0.9"/><path d="M3.6 4.6 7 7.4 10.4 4.6" fill="none" stroke="#fff" stroke-width="0.9"/></svg>
      mlindqvist@lindqvistnotes.com
    </div>
    <div class="contact">
      <svg class="icon" viewBox="0 0 14 14" aria-hidden="true"><circle cx="7" cy="7" r="6.5" fill="#1db3a0"/><path d="M7 3.2a2.4 2.4 0 0 1 2.4 2.4C9.4 7.4 7 10.4 7 10.4S4.6 7.4 4.6 5.6A2.4 2.4 0 0 1 7 3.2z" fill="#fff"/><circle cx="7" cy="5.6" r="0.9" fill="#1db3a0"/></svg>
      418 Alder Row Brookfield, OR 97214
    </div>
  </div>
</section>

</body>
</html>
```